Advertising company unique advertising platform

we need a logo design for a new company based in Australia Melbourne. We develop innovated advertising platform where consumer can use this platform to get regular discount, as business owner they can use this platform for free advertisement. Payment for this advertisement platform only payable every two weeks, when I generate revenue for their business

Industry/Entity Type

Advertising

Contact Information for Business Card

Dale Morven | Co-Founder |Managing Director
Suite 718 240 Wattlebrook Lane Melbourne Vic 3000

ABN 38 614 207 923
Tel: +61 0487 259 318 | Email: dale.morven@plivorantu.com

Font styles to use
Decorative
Script

Requirements
Must have
• Try few different design and some round corner business card
Should not have
• One round corner business card...try 4 different colour background not only black, make sure two side is designed. Be creative so imagine you are giving this to a client make sure has wow factor, if you can also try one design with engrave like all the logo, words look 3d feel
• The word Advertising Platform use attached file font

```html
<!DOCTYPE html>
<html lang="en">
<head>
<meta charset="utf-8">
<title>Plivorantu Business Card</title>
<link href="https://fonts.googleapis.com/css2?family=Roboto:wght@400;500&family=Roboto+Condensed:wght@500&display=swap" rel="stylesheet">
<style>
  :root {
    --backdrop: #4e3e33;
    --card-dark: #2b2b2b;
    --mint: #1de9a6;
    --mint-deep: #14d49c;
    --teal-soft: #55b0b3;
    --wave-blue: #6f99d4;
    --accent: #e4572e;
    --ink-light: #ffffff;
  }
  * { margin: 0; padding: 0; box-sizing: border-box; }
  html, body { width: 1200px; height: 960px; overflow: hidden; }
  body {
    background: var(--backdrop);
    font-family: "Roboto", Arial, sans-serif;
    position: relative;
  }
  .card {
    position: absolute;
    width: 600px;
    height: 342px;
    border-radius: 22px;
    overflow: hidden;
    box-shadow: 0 4px 10px rgba(0,0,0,0.35);
  }
  .card-front { left: 315px; top: 113px; background: var(--card-dark); }
  .card-back {
    left: 311px; top: 472px;
    background: linear-gradient(175deg, var(--teal-soft) 0%, var(--mint-deep) 100%);
  }
  .front-wave { position: absolute; inset: 0; }
  .brand-mark {
    position: absolute;
    display: flex;
    align-items: center;
    gap: 12px;
    font-family: "Roboto", Arial, sans-serif;
    font-weight: 500;
  }
  .brand-mark .brand-dot { border-radius: 50%; flex: none; }
  .card-front .brand-mark { left: 34px; top: 78px; font-size: 34px; color: var(--accent); }
  .card-front .brand-dot { width: 44px; height: 44px; background: var(--accent); }
  .holder {
    position: absolute;
    right: 28px;
    top: 24px;
    text-align: right;
    color: var(--ink-light);
    font-family: "Roboto Condensed", "Arial Narrow", sans-serif;
    font-weight: 500;
    text-transform: uppercase;
  }
  .holder-name { font-size: 21px; line-height: 26px; }
  .holder-role { font-size: 15.5px; line-height: 19px; }
  .contact {
    position: absolute;
    left: 33px;
    top: 188px;
    color: var(--ink-light);
    font-size: 14.5px;
    line-height: 18px;
  }
  .contact-group { margin-bottom: 7px; }
  .contact-line { display: flex; align-items: center; gap: 8px; }
  .contact-line svg { width: 13px; height: 13px; fill: var(--accent); flex: none; }
  .card-back .brand-mark {
    left: 0; right: 0; top: 142px;
    justify-content: center;
    font-size: 46px;
    color: var(--ink-light);
  }
  .card-back .brand-dot { width: 60px; height: 60px; background: var(--ink-light); }
  .website {
    position: absolute;
    left: 0; right: 0; top: 293px;
    text-align: center;
    color: var(--ink-light);
    font-size: 14px;
    letter-spacing: 4.6px;
  }
</style>
</head>
<body>
  <section class="card card-front">
    <svg class="front-wave" viewBox="0 0 600 342" aria-hidden="true">
      <defs>
        <linearGradient id="waveFill" x1="0" y1="0" x2="0.4" y2="1">
          <stop offset="0" stop-color="#1de9a6"/>
          <stop offset="0.55" stop-color="#3cc8b0"/>
          <stop offset="1" stop-color="#6f99d4"/>
        </linearGradient>
      </defs>
      <path d="M395 0 C 300 40, 300 130, 400 200 C 450 240, 450 300, 450 342 L600 342 L600 0 Z" fill="url(#waveFill)"/>
      <path d="M395 0 C 350 40, 350 120, 420 200 C 470 260, 460 310, 450 342" fill="none" stroke="#ffffff" stroke-width="2"/>
    </svg>
    <div class="brand-mark"><span class="brand-dot"></span>Brightway Hub</div>
    <div class="holder">
      <div class="holder-name">Dale Morven</div>
      <div class="holder-role">Co-Founder</div>
      <div class="holder-role">Managing Director</div>
    </div>
    <div class="contact">
      <div class="contact-group">
        <div>Plivorantu</div>
        <div>ABN 38 614 207 923</div>
      </div>
      <div class="contact-group">
        <div>Suite 718 240 Wattlebrook Lane</div>
        <div>Melbourne Vic 3000</div>
      </div>
      <div class="contact-line">
        <svg viewBox="0 0 24 24" aria-hidden="true"><path d="M6.6 10.8a15.1 15.1 0 0 0 6.6 6.6l2.2-2.2a1 1 0 0 1 1-.25 11.4 11.4 0 0 0 3.6.57 1 1 0 0 1 1 1V20a1 1 0 0 1-1 1A17 17 0 0 1 3 4a1 1 0 0 1 1-1h3.5a1 1 0 0 1 1 1c0 1.25.2 2.45.57 3.57a1 1 0 0 1-.25 1z"/></svg>
        <span>+61 0487 259 318</span>
      </div>
      <div class="contact-line">
        <svg viewBox="0 0 24 24" aria-hidden="true"><path d="M2 5h20v14H2z M2 5l10 8 10-8" /><path d="M3 6l9 7 9-7" fill="#2b2b2b"/></svg>
        <span>dale.morven@plivorantu.com</span>
      </div>
    </div>
  </section>

  <section class="card card-back">
    <div class="brand-mark"><span class="brand-dot"></span>Brightway Hub</div>
    <div class="website">www.plivorantu.com</div>
  </section>
</body>
</html>
```